Business Card Design

We need a business card designed for our new company. Prefer a black card with white logo & writing.

Contact Information for Business Card

Ted Galloway, address: 7-4812 Fernhollow Road, Abbotsford, BC, V3K 8R2, Office Phone: 604-712-3390, Cell: 604-947-2164, Email: ted@resinworkshub.ca

Colors

Designer to choose only greyscale colors for use in the design.

```html
<!DOCTYPE html>
<html lang="en">
<head>
<meta charset="utf-8">
<title>Resin Works Hub – Business Card</title>
<link rel="stylesheet" href="https://fonts.googleapis.com/css2?family=Montserrat:wght@400;500;700;800&display=swap">
<style>
  :root {
    --backdrop: #9b9b9b;
    --card-light: #ffffff;
    --card-dark: #212121;
    --ink: #111111;
    --ink-soft: #1c1c1c;
    --mark-on-dark: #0c0c0c;
  }
  * { margin: 0; padding: 0; box-sizing: border-box; }
  html, body {
    width: 1093px;
    height: 1200px;
    overflow: hidden;
    background: var(--backdrop);
    font-family: "Montserrat", Arial, sans-serif;
    color: var(--ink);
  }
  .card {
    position: absolute;
    left: 264px;
    width: 581px;
    height: 364px;
    border-radius: 18px;
  }
  .card--front { top: 225px; background: var(--card-light); }
  .card--back  { top: 616px; background: var(--card-dark); }

  .holder { position: absolute; left: 29px; top: 43px; }
  .holder__name { font-size: 20px; font-weight: 700; letter-spacing: 0.1px; line-height: 1.2; }
  .holder__role { font-size: 12.5px; font-weight: 400; margin-top: 2px; color: var(--ink-soft); }

  .brand {
    position: absolute;
    left: 386px;
    top: 40px;
    width: 170px;
    text-align: center;
    font-weight: 800;
    font-size: 22px;
    line-height: 1.05;
    letter-spacing: 0.5px;
    color: var(--ink);
  }

  .contacts {
    position: absolute;
    left: 28px;
    top: 255px;
    list-style: none;
    font-size: 12.5px;
    color: var(--ink-soft);
  }
  .contacts__item { display: flex; align-items: center; height: 22px; }
  .contacts__icon { width: 14px; height: 14px; margin-right: 8px; fill: var(--ink); }

  .address {
    position: absolute;
    left: 386px;
    top: 307px;
    font-size: 12.5px;
    line-height: 16px;
    font-style: normal;
    color: var(--ink-soft);
  }

  .brand--large {
    position: absolute;
    left: 0;
    right: 0;
    top: 128px;
    text-align: center;
    font-weight: 800;
    font-size: 46px;
    letter-spacing: 1px;
    line-height: 1.1;
    color: var(--mark-on-dark);
  }
</style>
</head>
<body>
  <section class="card card--front">
    <div class="holder">
      <p class="holder__name">Ted Galloway</p>
      <p class="holder__role">owner</p>
    </div>

    <div class="brand">RESIN WORKS<br>HUB</div>

    <ul class="contacts">
      <li class="contacts__item">
        <svg class="contacts__icon" viewBox="0 0 24 24" aria-hidden="true"><path d="M6.6 10.8a15.1 15.1 0 0 0 6.6 6.6l2.2-2.2a1 1 0 0 1 1-.25 11.4 11.4 0 0 0 3.6.57 1 1 0 0 1 1 1V20a1 1 0 0 1-1 1A17 17 0 0 1 3 4a1 1 0 0 1 1-1h3.5a1 1 0 0 1 1 1c0 1.25.2 2.45.57 3.57a1 1 0 0 1-.25 1z"/></svg>
        604-712-3390
      </li>
      <li class="contacts__item">
        <svg class="contacts__icon" viewBox="0 0 24 24" aria-hidden="true"><path d="M8 1h8a2 2 0 0 1 2 2v18a2 2 0 0 1-2 2H8a2 2 0 0 1-2-2V3a2 2 0 0 1 2-2zm0 3v14h8V4zm4 15.5a1.2 1.2 0 1 0 0 2.4 1.2 1.2 0 0 0 0-2.4z"/></svg>
        604-947-2164
      </li>
      <li class="contacts__item">
        <svg class="contacts__icon" viewBox="0 0 24 24" aria-hidden="true"><path d="M2 5h20v2l-10 6L2 7zm0 4.3 10 6 10-6V19H2z"/></svg>
        ted@resinworkshub.ca
      </li>
      <li class="contacts__item">
        <svg class="contacts__icon" viewBox="0 0 24 24" aria-hidden="true"><path d="M12 2a10 10 0 1 0 0 20 10 10 0 0 0 0-20zm-1 17.9A8 8 0 0 1 4.2 10.6L9 15.4v1a2 2 0 0 0 2 2zm6.9-2.5A2 2 0 0 0 16 16h-1v-3a1 1 0 0 0-1-1H8v-2h2a1 1 0 0 0 1-1V7h2a2 2 0 0 0 2-2v-.4a8 8 0 0 1 2.9 12.8z"/></svg>
        www.resinworkshub.ca
      </li>
    </ul>

    <address class="address">
      7-4812 Fernhollow Road,<br>
      Abbotsford, BC, V3K 8R2
    </address>
  </section>

  <section class="card card--back">
    <div class="brand--large">RESIN WORKS<br>HUB</div>
  </section>
</body>
</html>
```